Marwick Family Chiropractic Stationary

The letterhead and business card must have our logo.
We would like to see the logo used in different ways ( It can be expanded upon in the stationary.)
Please use the the same or similar colors.
Must be eye catching and memorable.
Must be easy to read

Reason: The doctor has been too busy to make any final decisions. He would like to give himself a little more time.

Target Market(s)

Chiropractic Healthcare

Industry/Entity Type

Business

Requirements
Must have
• Dr. Leonard Marwick D.C.
Chiropractor

860-555-0183

417 Birchfield Road, 2nd Floor
Vernon, CT 06091

drmarwick@marwickspine.example
www.marwickspine.example
www.facebook.com/MarwickFamilySpine
Should not have
• should not be difficult to read

```html
<!DOCTYPE html>
<html lang="en">
<head>
<meta charset="utf-8">
<title>Marwick Family Chiropractic – Business Cards</title>
<link rel="stylesheet" href="https://fonts.googleapis.com/css2?family=Montserrat:wght@600;700&family=Questrial&display=swap">
<style>
  :root {
    --stage: #b48a63;
    --label: #2a2118;
    --card-white: #ffffff;
    --card-brown: #2a211b;
    --card-black: #0b0b0b;
    --green: #2b9a47;
    --green-light: #9cc54b;
    --brown: #3b2f26;
    --taupe: #9a8f83;
    --ink: #3a3a3a;
    --white: #ffffff;
  }
  * { box-sizing: border-box; margin: 0; padding: 0; }
  html, body {
    width: 1200px; height: 788px; overflow: hidden;
    background: var(--stage);
  }
  .canvas { position: relative; width: 1200px; height: 788px; }
  .view-label {
    position: absolute; width: 525px; text-align: center;
    font: 20px "Questrial", sans-serif; color: var(--label);
  }
  .card {
    position: absolute; width: 525px; height: 300px;
    border-radius: 22px; overflow: hidden;
    box-shadow: 0 6px 14px rgba(0,0,0,.35);
  }
  .card--front { left: 54px; top: 74px; background: var(--card-white); }
  .card--back-1 { left: 622px; top: 74px; background: var(--card-white); }
  .card--back-2 { left: 54px; top: 445px; background: var(--card-brown); }
  .card--back-3 { left: 622px; top: 445px; background: var(--card-black); }

  .brand {
    position: absolute; text-align: center;
    font-family: "Montserrat", sans-serif; font-weight: 700;
    line-height: 1;
  }
  .brand__mark { display: block; margin: 0 auto; border-radius: 50%; }
  .brand__name { display: block; }
  .brand__tag { display: block; }

  .card--front .brand { left: 14px; top: 28px; width: 188px; color: var(--green); }
  .card--front .brand__mark { width: 86px; height: 86px; background: var(--green); margin-bottom: 40px; }
  .card--front .brand__name { font-size: 27px; }
  .card--front .brand__tag { font-size: 12px; margin-top: 6px; color: var(--brown); }

  .name-band {
    position: absolute; left: 244px; top: 147px; width: 280px; height: 50px;
    background: var(--green); color: var(--white);
    font-family: "Montserrat", sans-serif;
  }
  .name-band::after {
    content: ""; position: absolute; right: 0; top: 0; width: 27px; height: 100%;
    background: var(--brown);
  }
  .name-band__name { position: absolute; left: 9px; top: 8px; font-size: 15px; font-weight: 700; }
  .name-band__role { position: absolute; left: 9px; top: 30px; font-size: 12px; font-weight: 600; }

  .contact-list {
    position: absolute; left: 250px; top: 211px; list-style: none;
    font: 12.5px/18.5px "Questrial", sans-serif; color: var(--ink);
  }
  .contact-list li { display: flex; align-items: center; gap: 5px; }
  .contact-list svg { width: 10px; height: 10px; flex: none; }

  .address {
    position: absolute; left: 22px; top: 250px;
    font: 12.5px/18px "Questrial", sans-serif; color: var(--ink);
  }

  .card--back-1 .brand, .card--back-3 .brand { left: 0; width: 525px; top: 34px; }
  .card--back-1 .brand { color: var(--green); }
  .card--back-3 .brand { color: var(--green-light); }
  .card--back-1 .brand__mark, .card--back-3 .brand__mark { width: 96px; height: 96px; margin-bottom: 40px; }
  .card--back-1 .brand__mark { background: var(--green); }
  .card--back-3 .brand__mark { background: var(--green-light); }
  .card--back-1 .brand__name, .card--back-3 .brand__name { font-size: 31px; }
  .card--back-1 .brand__tag, .card--back-3 .brand__tag { font-size: 13.5px; margin-top: 7px; }
  .card--back-1 .brand__tag { color: var(--brown); }
  .card--back-3 .brand__tag { color: var(--taupe); }

  .card--back-2 .brand { left: 0; width: 525px; top: 98px; color: var(--green); }
  .card--back-2 .brand__name { font-size: 58px; }
  .card--back-2 .brand__tag { font-size: 24px; margin-top: 12px; letter-spacing: .5px; color: var(--white); }

  .web {
    position: absolute; left: 0; width: 525px; top: 262px; text-align: center;
    font: 15px "Questrial", sans-serif;
  }
  .card--back-1 .web { color: var(--ink); }
  .card--back-2 .web, .card--back-3 .web { color: var(--white); }
</style>
</head>
<body>
<main class="canvas">
  <p class="view-label" style="left:54px; top:34px;">Front</p>
  <p class="view-label" style="left:622px; top:34px;">Back - 1</p>
  <p class="view-label" style="left:54px; top:405px;">Back - 2</p>
  <p class="view-label" style="left:622px; top:405px;">Back - 3</p>

  <section class="card card--front">
    <div class="brand">
      <span class="brand__mark"></span>
      <span class="brand__name">MARWICK</span>
      <span class="brand__tag">FAMILY CHIROPRACTIC</span>
    </div>
    <div class="name-band">
      <span class="name-band__name">Dr. Leonard Marwick D.C.</span>
      <span class="name-band__role">Chiropractor</span>
    </div>
    <ul class="contact-list">
      <li><svg viewBox="0 0 10 10"><circle cx="5" cy="5" r="4.3" fill="none" stroke="#2b9a47" stroke-width="1.2"/><path d="M3.5 3c0 2 1.5 3.5 3.5 3.5" stroke="#2b9a47" stroke-width="1.2" fill="none"/></svg>860-555-0183</li>
      <li><svg viewBox="0 0 10 10"><rect x="0.6" y="2" width="8.8" height="6" fill="none" stroke="#2b9a47" stroke-width="1.1"/><path d="M0.6 2 5 5.5 9.4 2" fill="none" stroke="#2b9a47" stroke-width="1.1"/></svg>drmarwick@marwickspine.example</li>
      <li><svg viewBox="0 0 10 10"><circle cx="5" cy="5" r="4.5" fill="#2b9a47"/></svg>www.marwickspine.example</li>
      <li><svg viewBox="0 0 10 10"><rect x="1" y="1" width="8" height="8" fill="#2b9a47"/></svg>social.marwickspine.example/family</li>
    </ul>
    <p class="address">417 Birchfield Road<br>Suite 2, Ashmere Valley 06091</p>
  </section>

  <section class="card card--back-1">
    <div class="brand">
      <span class="brand__mark"></span>
      <span class="brand__name">MARWICK</span>
      <span class="brand__tag">FAMILY CHIROPRACTIC</span>
    </div>
    <p class="web">www.marwickspine.example</p>
  </section>

  <section class="card card--back-2">
    <div class="brand">
      <span class="brand__name">MARWICK</span>
      <span class="brand__tag">FAMILY CHIROPRACTIC</span>
    </div>
    <p class="web">www.marwickspine.example</p>
  </section>

  <section class="card card--back-3">
    <div class="brand">
      <span class="brand__mark"></span>
      <span class="brand__name">MARWICK</span>
      <span class="brand__tag">FAMILY CHIROPRACTIC</span>
    </div>
    <p class="web">www.marwickspine.example</p>
  </section>
</main>
</body>
</html>
```